Poster & Banner for Outback tour company

Poster needed for tour company in the Australian outback. We will need it in an A2 format and if possible a larger banner format as Well please. It needs the Galah Tours logo but also the other logos (less obvious). It also needs to feature the WanderRate logo (uploaded).

The poster needs a list of the tours we offer as well as some of the pictures uploaded.

List of tours:

- Premium Tour of the Town and the Breakaways $99
- Coober Pedy Highlights Tour $85
- Sunset Breakaways Tour $60
- Underground Noodling Tour $50

Industry/Entity Type

Tour Company

Font styles to use
Serif

Colors

Designer to choose colors to be used in the design.

Requirements
Must have
• Galah Tours logo/List of tours/

```html
<!DOCTYPE html>
<html lang="en">
<head>
<meta charset="utf-8">
<title>Explore Coober Pedy with Galah Tours</title>
<link rel="stylesheet" href="https://fonts.googleapis.com/css2?family=Lato:wght@300;400;700;900&display=swap">
<style>
  :root {
    --navy: #234a6c;
    --navy-deep: #1d3f5e;
    --white: #ffffff;
    --ink: #1f1f1f;
    --orange: #f3921f;
    --badge-green: #34e0a1;
    --sky-top: #1f4f86;
    --sky-mid: #4f8fd0;
    --earth-light: #d89a5e;
    --earth-dark: #9a4a22;
    --brand-brown: #5a2e12;
  }
  * { box-sizing: border-box; margin: 0; padding: 0; }
  html, body { width: 848px; height: 1200px; overflow: hidden; background: var(--navy); }
  body { font-family: "Lato", Arial, sans-serif; }
  .poster { position: relative; width: 848px; height: 1200px; background: var(--navy); overflow: hidden; }

  .hero { position: absolute; left: 0; top: 0; width: 848px; height: 582px; }

  .award-badge {
    position: absolute; left: 40px; top: 44px; width: 74px; height: 86px;
    background: var(--badge-green); border: 2px solid var(--white);
  }

  .brand-box {
    position: absolute; left: 628px; top: 45px; width: 172px; height: 85px;
    background: var(--white); border-radius: 8px;
    display: flex; align-items: center; justify-content: center; gap: 7px;
  }
  .brand-box .mark { width: 14px; height: 14px; background: var(--orange); }
  .brand-box .name { font-weight: 900; font-size: 20px; color: var(--brand-brown); letter-spacing: 0.3px; }

  .headline {
    position: absolute; left: 0; width: 848px; top: 404px; text-align: center; color: var(--white);
    text-shadow: 0 2px 10px rgba(0,0,0,0.35);
  }
  .headline .line1 { font-size: 49px; font-weight: 300; line-height: 62px; letter-spacing: -0.5px; }
  .headline .line1 strong { font-weight: 900; }
  .headline .line2 { font-size: 50px; font-weight: 900; line-height: 62px; }

  .tours { position: absolute; top: 591px; left: 0; width: 848px; }
  .tour-card {
    position: absolute; top: 0; width: 184px; height: 354px;
    background: var(--white); border-radius: 92px;
    box-shadow: 0 10px 22px rgba(0,0,0,0.35);
  }
  .tour-card .photo {
    position: absolute; left: 13px; top: 12px; width: 158px; height: 170px;
    border-radius: 79px 79px 18px 18px;
  }
  .tour-card h2 {
    position: absolute; left: 16px; right: 16px; top: 197px;
    text-align: center; font-size: 19px; font-weight: 700; line-height: 24px; color: var(--ink);
  }
  .tour-card .price {
    position: absolute; left: 54px; top: 302px; width: 76px; height: 76px; border-radius: 50%;
    background: var(--orange); color: var(--white);
    display: flex; align-items: center; justify-content: center;
    font-size: 32px; font-weight: 900;
  }
  .card-1 { left: 24px; } .card-2 { left: 230px; } .card-3 { left: 435px; } .card-4 { left: 639px; }
  .photo-cave { background: linear-gradient(180deg, #b86a3e 0%, #6f9bd0 35%, #c7a07a 80%, #a45a32 100%); }
  .photo-church { background: linear-gradient(180deg, #8d5a36 0%, #c48a4a 45%, #7a3a20 100%); }
  .photo-sunset { background: linear-gradient(180deg, #1b2a55 0%, #4a4f8a 45%, #e0803a 80%, #231a16 100%); }
  .photo-tunnel { background: linear-gradient(135deg, #9aa3a0 0%, #c9d2cc 40%, #5a4a3a 100%); }

  .tagline {
    position: absolute; top: 990px; left: 0; width: 848px; text-align: center;
    color: var(--white); font-size: 31px; font-weight: 400;
  }

  .partners-band { position: absolute; left: 0; top: 1040px; width: 848px; height: 132px; }
  .partners {
    position: absolute; left: 100px; top: 1070px; width: 640px; height: 82px;
    display: flex; align-items: center;
  }
  .partner {
    flex: 1; text-align: center; font-size: 16px; font-weight: 700; color: var(--earth-dark);
  }
  .divider { width: 1.5px; height: 82px; background: var(--ink); }
  .footer-strip { position: absolute; left: 0; top: 1172px; width: 848px; height: 28px; background: var(--navy); }
</style>
</head>
<body>
<main class="poster">
  <svg class="hero" viewBox="0 0 848 582" role="img" aria-label="Photograph of the colourful Breakaways hills under a blue outback sky">
    <defs>
      <linearGradient id="heroFill" x1="0" y1="0" x2="0" y2="1">
        <stop offset="0" stop-color="#1f4a7e"/>
        <stop offset="0.45" stop-color="#4e8fcf"/>
        <stop offset="0.56" stop-color="#9bb6c8"/>
        <stop offset="0.62" stop-color="#d7a36a"/>
        <stop offset="0.8" stop-color="#b5602e"/>
        <stop offset="1" stop-color="#8a5a38"/>
      </linearGradient>
    </defs>
    <path d="M0 0 H848 V444 Q424 730 0 444 Z" fill="url(#heroFill)"/>
  </svg>

  <div class="award-badge" role="img" aria-label="WanderRate award badge"></div>

  <div class="brand-box">
    <span class="mark"></span>
    <span class="name">GALAH TOURS</span>
  </div>

  <h1 class="headline">
    <div class="line1">Explore <strong>Coober Pedy</strong> with</div>
    <div class="line2">Galah Tours</div>
  </h1>

  <section class="tours">
    <article class="tour-card card-1">
      <div class="photo photo-cave" role="img" aria-label="Tour vehicle seen through a sandstone cave opening"></div>
      <h2>Premium Tour of the Town and the Breakaways</h2>
      <div class="price">$99</div>
    </article>
    <article class="tour-card card-2">
      <div class="photo photo-church" role="img" aria-label="Underground church with painted icons"></div>
      <h2>Coober Pedy Highlights Tour</h2>
      <div class="price">$85</div>
    </article>
    <article class="tour-card card-3">
      <div class="photo photo-sunset" role="img" aria-label="Mining truck sign silhouetted at sunset"></div>
      <h2>Sunset Breakaways Tour</h2>
      <div class="price">$60</div>
    </article>
    <article class="tour-card card-4">
      <div class="photo photo-tunnel" role="img" aria-label="Explorer in a hat looking into an underground mine tunnel"></div>
      <h2>Underground Noodling Tour</h2>
      <div class="price">$50</div>
    </article>
  </section>

  <p class="tagline">Coober Pedy’s best-rated tour company.</p>

  <svg class="partners-band" viewBox="0 0 848 132" aria-hidden="true">
    <path d="M0 22 Q424 -12 848 22 V132 H0 Z" fill="#ffffff"/>
  </svg>
  <div class="partners">
    <span class="partner">Opal Ridge Resort</span>
    <span class="divider"></span>
    <span class="partner">Trailhead Parks</span>
    <span class="divider"></span>
    <span class="partner">Horizon Stays</span>
    <span class="divider"></span>
    <span class="partner">Dustbowl Lodge</span>
  </div>
  <div class="footer-strip"></div>
</main>
</body>
</html>
```